business card deign

Logo needs the following on it.
1. attached logo
2. Tagline - "From chilled drinks to lively nights...we bring it all!"
3. Name- Dalton Pikes, Founder and CPO
4. Address - 412 E. Carver Avenue, Ste 2207, Tampa, FL. 33917
5. Phone - 555.318.4726

```html
<!DOCTYPE html>
<html lang="en">
<head>
<meta charset="utf-8">
<title>Hoplin Business Card</title>
<link rel="stylesheet" href="https://fonts.googleapis.com/css2?family=Montserrat:wght@700&family=Roboto:wght@400&display=swap">
<style>
  :root {
    --backdrop: #2b2b2b;
    --card-green: #0f4a43;
    --card-cream: #f1e6de;
    --gold: #c98d3c;
    --ink: #111111;
    --ink-soft: #4a4a4a;
    --rule: #8a8480;
  }
  * { box-sizing: border-box; margin: 0; padding: 0; }
  html, body { width: 1200px; height: 825px; overflow: hidden; }
  body {
    background: var(--backdrop);
    display: flex;
    align-items: center;
    justify-content: center;
    gap: 48px;
    font-family: "Roboto", sans-serif;
  }
  .card {
    width: 525px;
    height: 300px;
    position: relative;
    box-shadow: 0 18px 40px rgba(0,0,0,0.45);
  }
  .card-back {
    background: var(--card-green);
    display: flex;
    align-items: center;
    justify-content: center;
  }
  .back-wordmark {
    font-family: "Montserrat", sans-serif;
    font-weight: 700;
    font-size: 44px;
    letter-spacing: 12px;
    color: var(--gold);
    padding-left: 12px;
  }
  .card-front {
    background: var(--card-cream);
    padding: 40px 36px 0 36px;
  }
  .front-main {
    display: flex;
    height: 180px;
  }
  .brand-block {
    width: 190px;
    display: flex;
    align-items: flex-end;
    justify-content: center;
    gap: 10px;
    padding-bottom: 6px;
  }
  .brand-dot {
    width: 14px; height: 14px;
    border-radius: 50%;
    background: var(--ink);
    margin-bottom: 6px;
  }
  .brand-name {
    font-family: "Montserrat", sans-serif;
    font-weight: 700;
    font-size: 24px;
    letter-spacing: 8px;
    color: var(--ink);
  }
  .divider {
    width: 1px;
    background: var(--rule);
    margin: 0 26px 0 14px;
  }
  .contact {
    color: var(--ink-soft);
    font-size: 12.5px;
    line-height: 1.3;
  }
  .person-name {
    font-family: "Montserrat", sans-serif;
    font-weight: 700;
    font-size: 19px;
    color: var(--ink);
    letter-spacing: 0.3px;
  }
  .person-title { margin-bottom: 12px; }
  .address { margin-bottom: 12px; }
  .contact-line { display: flex; align-items: center; gap: 8px; }
  .contact-line svg { width: 12px; height: 12px; fill: var(--ink); }
  .tagline {
    text-align: center;
    color: var(--ink-soft);
    font-size: 13px;
    margin-top: 26px;
  }
</style>
</head>
<body>
  <section class="card card-back">
    <span class="back-wordmark">HOPLIN</span>
  </section>

  <section class="card card-front">
    <div class="front-main">
      <div class="brand-block">
        <span class="brand-dot"></span>
        <span class="brand-name">HOPLIN</span>
      </div>
      <div class="divider"></div>
      <div class="contact">
        <div class="person-name">DALTON PIKES</div>
        <div class="person-title">Founder and CPO</div>
        <div class="address">412 E. Carver Avenue,<br>Ste 2207, Tampa, FL. 33917</div>
        <div class="contact-line">
          <svg viewBox="0 0 24 24" aria-hidden="true"><path d="M6.6 10.8a15.1 15.1 0 0 0 6.6 6.6l2.2-2.2a1 1 0 0 1 1-.25 11.4 11.4 0 0 0 3.6.57 1 1 0 0 1 1 1V20a1 1 0 0 1-1 1A17 17 0 0 1 3 4a1 1 0 0 1 1-1h3.5a1 1 0 0 1 1 1c0 1.25.2 2.45.57 3.57a1 1 0 0 1-.25 1z"/></svg>
          <span>555.318.4726</span>
        </div>
        <div class="contact-line">
          <svg viewBox="0 0 24 24" aria-hidden="true"><path d="M2 5h20v14H2z M2 5l10 8 10-8" /></svg>
          <span>info@hoplinco.com</span>
        </div>
      </div>
    </div>
    <p class="tagline">From chilled drinks to lively nights...we bring it all!</p>
  </section>
</body>
</html>
```